Corporate Business Card

Very professional, Modern, Not to busy, include phone address email, website
(253) 617-4930, 18761 52nd Avenue S, Kent, WA 98047, martin@plumlinegroup.com, varkoworks.com

Target Market(s)

Manufacturing

Industry/Entity Type

Aero, machining, manufacturing, Off road racing

Contact Information for Business Card

Phone, address email, website

```html
<!DOCTYPE html>
<html lang="en">
<head>
<meta charset="utf-8">
<title>Varko Works – Business Card</title>
<link rel="stylesheet" href="https://fonts.googleapis.com/css2?family=Roboto:wght@400;700&family=Exo+2:wght@700&display=swap">
<style>
  :root {
    --backdrop: #2a2a2a;
    --navy: #2c3a6a;
    --navy-deep: #243260;
    --navy-light: #34457a;
    --red: #b71f24;
    --red-deep: #a81c21;
    --silver: #a7a9ad;
    --white: #ffffff;
  }
  * { margin: 0; padding: 0; box-sizing: border-box; }
  html, body { width: 1200px; height: 1138px; overflow: hidden; background: var(--backdrop); }
  body { position: relative; font-family: "Roboto", Arial, sans-serif; }

  .card {
    position: absolute;
    border-radius: 16px;
    overflow: hidden;
  }

  /* Back side */
  .card-back {
    left: 274px; top: 186px; width: 623px; height: 376px;
    background: var(--navy);
  }
  .card-back .tonal-pattern {
    position: absolute; inset: 0;
    background: linear-gradient(160deg, var(--navy-light) 0%, var(--navy) 50%, var(--navy-deep) 100%);
  }
  .card-back .brand-name {
    position: absolute; left: 54px; top: 282px;
    font-family: "Roboto", Arial, sans-serif;
    font-weight: 700; font-size: 38px; letter-spacing: 1px;
    color: var(--white);
  }

  /* Front side */
  .card-front {
    left: 276px; top: 608px; width: 618px; height: 374px;
    background: var(--navy);
  }
  .card-front .wave { position: absolute; inset: 0; }
  .card-front .brand-name {
    position: absolute; left: 0; right: 0; top: 64px;
    text-align: center;
    font-family: "Roboto", Arial, sans-serif;
    font-weight: 700; font-size: 46px; letter-spacing: 2px;
    color: var(--white);
  }
  .holder-name {
    position: absolute; left: 34px; top: 282px;
    font-family: "Exo 2", "Roboto", sans-serif;
    font-weight: 700; font-size: 24px; line-height: 24px;
    color: var(--white); text-transform: uppercase;
  }
  .contact-list {
    position: absolute; right: 32px; top: 234px;
    list-style: none; text-align: right;
    color: var(--white); font-size: 16px; line-height: 24px;
  }
  .contact-list li { display: flex; justify-content: flex-end; align-items: center; gap: 10px; }
  .contact-list svg { width: 14px; height: 14px; fill: var(--white); }
  .contact-list .address { margin-top: 4px; margin-right: -9px; }
</style>
</head>
<body>

  <section class="card card-back" aria-label="Card back">
    <div class="tonal-pattern" role="img" aria-label="Tonal repeating pattern of the company name on navy"></div>
    <div class="brand-name">VARKO WORKS</div>
  </section>

  <section class="card card-front" aria-label="Card front">
    <svg class="wave" viewBox="0 0 618 374" preserveAspectRatio="none" aria-hidden="true">
      <path d="M0 136 C 120 190, 260 200, 400 175 C 490 158, 560 150, 618 162 L618 172 C 540 162, 470 172, 400 188 C 270 214, 120 210, 0 148 Z" fill="var(--silver)"/>
      <path d="M0 160 C 140 220, 300 210, 420 186 C 510 170, 570 166, 618 168 L618 374 L0 374 Z" fill="var(--red)"/>
      <rect x="0" y="280" width="618" height="94" fill="var(--red-deep)" opacity="0.35"/>
    </svg>

    <div class="brand-name">VARKO WORKS</div>

    <div class="holder-name">Martin<br>Hale</div>

    <ul class="contact-list">
      <li>(253) 617-4930
        <svg viewBox="0 0 16 16" aria-hidden="true"><path d="M3.5 1.5l2.5 0 1 3.5-1.6 1.2a9 9 0 0 0 4.4 4.4L11 9l3.5 1v2.5c0 1-1 2-2 2A11.5 11.5 0 0 1 1.5 3.5c0-1 1-2 2-2z"/></svg>
      </li>
      <li>www.varkoworks.com
        <svg viewBox="0 0 16 16" aria-hidden="true"><circle cx="8" cy="8" r="6.5" fill="none" stroke="#fff" stroke-width="1.4"/><path d="M1.5 8h13M8 1.5c-3 3.5-3 9.5 0 13M8 1.5c3 3.5 3 9.5 0 13" fill="none" stroke="#fff" stroke-width="1.2"/></svg>
      </li>
      <li>martin@plumlinegroup.com
        <svg viewBox="0 0 16 16" aria-hidden="true"><rect x="1" y="3" width="14" height="10" rx="1"/><path d="M1.5 3.5L8 9l6.5-5.5" fill="none" stroke="#b71f24" stroke-width="1.3"/></svg>
      </li>
      <li class="address">18761 52nd Avenue S, Kent, WA 98047</li>
    </ul>
  </section>

</body>
</html>
```